Marwick Law Letterhead

We need a new letterhead design for a Law Firm. The address for the law firm is 1475 Calloway Street, Suite 210, Houston, Texas 77041. Phone Number: 832-361-9027; Fax Number: 832-614-7359. The logo is uploaded to the project.

```html
<!DOCTYPE html>
<html lang="en">
<head>
<meta charset="utf-8">
<title>Marwick Law Letterhead</title>
<link href="https://fonts.googleapis.com/css2?family=Arimo:wght@400;700&family=Libre+Baskerville:wght@400;700&display=swap" rel="stylesheet">
<style>
  :root {
    --navy: #1b2c5c;
    --red: #c8202a;
    --ink: #1a1a1a;
    --paper: #ffffff;
    --backdrop: #e9e6e2;
  }
  html, body {
    margin: 0;
    padding: 0;
    width: 1200px;
    height: 900px;
    overflow: hidden;
    background: var(--backdrop);
  }
  .letterhead {
    position: absolute;
    left: 267px;
    top: 20px;
    width: 666px;
    height: 860px;
    background: var(--paper);
    box-shadow: 0 4px 18px rgba(0,0,0,0.18);
    overflow: hidden;
    font-family: "Arimo", Arial, sans-serif;
    color: var(--ink);
  }
  .brand {
    position: absolute;
    left: 72px;
    top: 50px;
    display: flex;
    align-items: center;
    gap: 10px;
  }
  .brand-mark {
    width: 24px;
    height: 24px;
    background: var(--red);
  }
  .brand-name {
    font-family: "Libre Baskerville", Georgia, serif;
    font-weight: 400;
    font-size: 24px;
    color: var(--navy);
    letter-spacing: 0.4px;
  }
  .contact {
    position: absolute;
    left: 449px;
    top: 37px;
    font-family: "Libre Baskerville", Georgia, serif;
    font-style: normal;
    font-weight: 700;
    font-size: 9.5px;
    letter-spacing: 0.6px;
    color: var(--navy);
    line-height: 14px;
  }
  .contact-row {
    display: flex;
    align-items: flex-start;
    gap: 3px;
    margin-bottom: 3px;
  }
  .contact-row svg { flex: none; margin-top: 2px; }
  .letter {
    position: absolute;
    left: 70px;
    top: 174px;
    width: 529px;
    font-size: 14px;
    line-height: 20.6px;
  }
  .letter p { margin: 0; }
  .date { margin-bottom: 32px !important; }
  .recipient-name { font-weight: 700; font-size: 15px; }
  .recipient { margin-bottom: 40px !important; }
  .body-copy { text-align: justify; }
  .body-copy + .body-copy { margin-top: 20.6px; }
  .signature {
    display: block;
    width: 86px;
    height: 22px;
    margin: 48px 0 6px;
    background: linear-gradient(90deg, rgba(40,40,40,0.18), rgba(40,40,40,0.08));
    border-radius: 3px;
  }
  .sender { font-weight: 700; font-size: 15px; }
  .footer-band {
    position: absolute;
    left: 0;
    bottom: 0;
    width: 100%;
    height: 22px;
    background: var(--navy);
    border-top: 4px solid var(--red);
  }
</style>
</head>
<body>
  <main class="letterhead">
    <header>
      <div class="brand">
        <span class="brand-mark"></span>
        <span class="brand-name">Marwick Law</span>
      </div>
      <address class="contact">
        <div class="contact-row">
          <svg width="10" height="10" viewBox="0 0 24 24"><path fill="#c8202a" d="M6.6 10.8a15.1 15.1 0 0 0 6.6 6.6l2.2-2.2a1 1 0 0 1 1-.25 11.4 11.4 0 0 0 3.6.57 1 1 0 0 1 1 1V20a1 1 0 0 1-1 1A17 17 0 0 1 3 4a1 1 0 0 1 1-1h3.5a1 1 0 0 1 1 1c0 1.25.2 2.45.57 3.57a1 1 0 0 1-.25 1z"/></svg>
          <span>832-361-9027</span>
        </div>
        <div class="contact-row">
          <svg width="10" height="10" viewBox="0 0 24 24"><path fill="#c8202a" d="M7 3h8l2 2v4H7zM4 9h16a2 2 0 0 1 2 2v7H2v-7a2 2 0 0 1 2-2zm3 6h10v5H7z"/></svg>
          <span>832-614-7359</span>
        </div>
        <div class="contact-row">
          <svg width="10" height="10" viewBox="0 0 24 24"><circle cx="12" cy="12" r="11" fill="#c8202a"/><path fill="#fff" d="M12 5a4.5 4.5 0 0 0-4.5 4.5C7.5 13 12 18 12 18s4.5-5 4.5-8.5A4.5 4.5 0 0 0 12 5zm0 6.2a1.7 1.7 0 1 1 0-3.4 1.7 1.7 0 0 1 0 3.4z"/></svg>
          <span>1475 Calloway Street, Suite 210,<br>Houston, Texas 77041</span>
        </div>
      </address>
    </header>

    <article class="letter">
      <p class="date">4th September 20XX</p>
      <p class="recipient">
        <span class="recipient-name">Ronny Reader</span><br>
        CEO, Company Name<br>
        123 Address St<br>
        Anytown, ST 12345
      </p>
      <p>Dear Mr. Reader,</p>
      <p class="body-copy">Lorem ipsum dolor sit amet, consectetuer adipiscing elit, sed diam nonummy nibh euismod tincidunt ut laoreet dolore magna aliquam erat volutpat. Ut wisi enim ad minim veniam, quis nostrud exerci tation ullamcorper suscipit lobortis nisl ut aliquip ex ea commodo consequat.</p>
      <p class="body-copy">Duis autem vel eum iriure dolor in hendrerit in vulputate velit esse molestie consequat, vel illum dolore eu feugiat nulla facilisis at vero eros et accumsan.</p>
      <p class="body-copy">Nam liber tempor cum soluta nobis eleifend option congue nihil imperdiet doming id quod mazim placerat facer possim assum. Typi non habent claritatem insitam; est usus legentis in iis qui facit eorum claritatem. Investigationes demonstraverunt lectores legere me lius quod ii legunt saepius.</p>
      <p>Sincerely,</p>
      <span class="signature" role="img" aria-label="Handwritten signature"></span>
      <p class="sender">Your Name</p>
    </article>

    <footer class="footer-band"></footer>
  </main>
</body>
</html>
```